Quimbly Needs a 1 Page Redesign with UI/UX Elements

Quimbly is a GIF creation and sharing site. We are upgrading one of our main responsive website pages. [Please see: http://quimblyzone.net/R-4TzLa for an example]

Need design versions for Desktop, tablet & mobile.

Also need frontend development to implement page. Currently on Foundation framework.

There are many functions/nav elements that need to be on this page in an uncluttered and clear manner. Not all of functions need to be shown at all times. Need a designer with UI/UX background to incorporate these and make it easy to navigate for the user.

The designer needs to be familiar with the site to understand each function. Color scheme will remain the same as current site.

If there are Dropdowns/collapsed or hidden features - need to know how they look when opened.

Target Market(s)

Quimbly has a varied demographic but focuses on under 25.

Coding

Coded - Design and coding required

Number of Pages Required

1 page

Font styles to use
Sans Serif

Requirements
Must have
• The top and bottom nav bars must stay the same. We are not redesigning the whole site yet, just that page.
• This page is developed with sharing in mind. Our top 3 actions are highlighted below. Be creative & think about user experience as our #1 priority
• Desktop
•  SOCIAL SHARE BUTTONS Zentrova/Plinkit/Voxmora/Brolendar
•  Download Button
•  Create a GIF Button
• OTHER FEATURES THAT MUST BE INCLUDED
• Share This With Friends pop up
• Title of GIF
• Added XX days ago by XXXX in XXX
• Source
• Thumbs up votes showing numerically (no down vote thumb)
• Total Views
• Embed Links: direct, website, message board, markdown
• NSFW Flag
• MP4 to GIF toggle
• Next arrows to scroll through GIFs
• Scroll thumbnail bar for like GIFs at the bottom of the page
• NEW FEATURES TO IMPLEMENT
• Favorite (bookmark Option)
• LOGGED IN USERS:
• Logged in users also have Private Button & Delete Button
• MOBILE
• We would like to keep the mobile page as minimalist as possible.
• Download button
• Create a GIF button
• Sharing button: Drovanel, Zentrova, Plinkit, Voxmora,
• Share Via SMS
• (Please incorporate the share buttons in a creative & clean way)
• Three dots that would open up to reveal tags
• Thumbnail scroll at bottom for GIFs in the same category
Nice to have
• Be creative with how the page features are laid out. We want it to be easy for users to navigate & clear what actions are there.
Should not have
• Basically anything that is on the page now. The buttons don't look like buttons & there is no drive to any actions (like sharing). Please see attached file for what NOT to do.

```html
<!DOCTYPE html>
<html lang="en">
<head>
<meta charset="utf-8">
<title>Quimbly – Make a GIF</title>
<link href="https://fonts.googleapis.com/css2?family=Open+Sans:wght@400;600;700&display=swap" rel="stylesheet">
<style>
:root{
  --yellow:#f6c414;
  --yellow-dark:#e8a800;
  --dark:#333333;
  --text:#444444;
  --line:#dddddd;
  --panel:#f4f4f4;
  --zentrova:#3b5998;
  --plinkit:#1da1f2;
  --voxmora:#d9342b;
  --drovanel:#f39c12;
  --linkora:#0e76a8;
  --fb-panel:#5b7fd1;
  --tw-panel:#3bb9ef;
}
*{box-sizing:border-box;margin:0;padding:0}
html,body{width:954px;height:1200px;overflow:hidden}
body{position:relative;font-family:"Open Sans",Arial,sans-serif;color:var(--text);background:#fff;font-size:9px}
.abs{position:absolute}

/* header */
.topbar{left:0;top:0;width:954px;height:59px;background:rgba(40,40,40,.85);z-index:3}
.logo{left:80px;top:17px;display:flex;align-items:center;gap:6px;color:#fff;font-weight:700;font-size:18px;z-index:4}
.logo .mark{width:22px;height:22px;background:var(--yellow);border-radius:3px}
.nav{left:271px;top:24px;display:flex;gap:21px;color:#ddd;font-size:9px;z-index:4}
.btn-login{left:716px;top:17px;width:58px;height:25px;background:#eee;color:#444;font-size:9.5px;display:flex;align-items:center;justify-content:center;border-radius:2px;z-index:4}
.btn-signup{left:778px;top:17px;width:62px;height:25px;background:var(--yellow);color:#333;font-size:9.5px;display:flex;align-items:center;justify-content:center;border-radius:2px;z-index:4}
.btn-search{left:848px;top:17px;width:26px;height:25px;background:#444;display:flex;align-items:center;justify-content:center;border-radius:2px;z-index:4}

/* hero */
.hero{left:0;top:0;width:954px;height:459px;background:linear-gradient(180deg,#6f8a55 0%,#b9a48c 35%,#8a97a8 65%,#c9c6c0 100%)}
.hero-title{left:0;top:158px;width:954px;text-align:center;color:#fff;font-weight:700;font-size:34px;letter-spacing:.5px}
.hero-sub{left:0;top:198px;width:954px;text-align:center;color:#fff;font-size:10px}
.hero-social{left:0;top:228px;width:954px;display:flex;justify-content:center;gap:6px}
.chip{height:20px;padding:0 5px;color:#fff;font-size:8px;font-weight:600;display:flex;align-items:center}
.hero-cta{left:374px;top:265px;width:205px;height:44px;background:linear-gradient(#f9cf2a,var(--yellow-dark));color:#333;font-weight:700;font-size:15px;display:flex;align-items:center;justify-content:center;border-radius:2px}
.hero-arrow{top:214px;width:38px;height:35px;border:2px solid #fff;border-radius:50%;display:flex;align-items:center;justify-content:center}

/* sections */
.section-title{left:83px;color:#333;font-size:18px;font-weight:600}
.pager{left:836px;display:flex;gap:3px}
.pager span{width:14px;height:14px;border:1px solid #bbb;border-radius:50%;display:flex;align-items:center;justify-content:center}

.feature{left:78px;top:517px;width:790px;height:267px;background:var(--panel);border:1px solid var(--line)}
.feature-media{left:21px;top:16px;width:355px;height:228px;background:radial-gradient(circle at 60% 45%,#c9b39a 0%,#8fb04a 45%,#4f7d1f 100%)}
.info{left:408px;top:18px;width:310px}
.info h2{font-size:14px;font-weight:600;color:#444;margin-bottom:11px}
.info p{font-size:8.5px;margin-bottom:11px}
.stats{display:flex;gap:16px;font-size:8.5px}
.rule{height:1px;background:#ddd;margin:14px 0 15px}
.share-row{display:flex;align-items:center;gap:6px;font-size:8.5px}
.share-row .chip{height:22px}
.actions{left:408px;top:215px;display:flex;gap:10px}
.toggle{display:flex;height:23px}
.toggle span{padding:0 9px;display:flex;align-items:center;font-size:8px;color:#fff;background:var(--dark)}
.toggle span.on{background:var(--yellow);color:#333}
.action{height:23px;padding:0 10px;background:var(--dark);color:#fff;font-size:8px;display:flex;align-items:center}

.thumbs{left:84px;top:848px;display:flex;gap:8px}
.thumb{width:150px;height:87px}

/* feeds */
.feed{top:968px;width:381px;height:106px;border:1px solid var(--line);background:#fff}
.feed-tag{left:0;top:0;width:81px;height:104px;color:#fff;font-size:12px;text-align:center;display:flex;flex-direction:column;align-items:center;justify-content:center;gap:6px;line-height:1.25}
.avatar{left:88px;top:11px;width:34px;height:34px;background:#ccd3dd}
.comment-box{left:128px;top:11px;width:241px;height:63px;border:1px solid #ddd;background:linear-gradient(#fff,#f3f3f3);color:#999;font-size:7.5px;padding:7px 9px}
.comment-btn{left:128px;top:79px;width:46px;height:15px;background:#4c67a1;color:#fff;font-size:7px;font-weight:700;display:flex;align-items:center;justify-content:center}
.tweet-media{left:88px;top:9px;width:115px;height:86px;background:linear-gradient(135deg,#8fb7d6,#e4c3a8)}
.tweet{left:214px;top:11px;width:155px;font-size:7.5px;line-height:1.45}
.tweet a{color:var(--plinkit);text-decoration:none}

/* footer */
.footer{left:0;top:1113px;width:954px;height:83px;background:var(--dark)}
.footer-links{left:79px;top:24px;color:#ddd;font-size:8.5px;display:flex;gap:6px}
.copyright{left:79px;top:46px;color:#ccc;font-size:8.5px}
.footer-social{right:80px;top:29px;display:flex;gap:5px}
.footer-social .chip{height:22px;font-size:7.5px;padding:0 4px}
.footer-band{left:0;top:1196px;width:954px;height:4px;background:var(--yellow)}

.bookmark{left:927px;top:511px;width:27px;height:115px;background:var(--yellow);color:#fff;font-size:7px;writing-mode:vertical-rl;transform:rotate(180deg);display:flex;align-items:center;justify-content:center}
</style>
</head>
<body>

<div class="abs hero" role="img" aria-label="Photo of a group of smiling friends sitting outdoors at a skate park"></div>

<header class="abs topbar"></header>
<div class="abs logo"><span class="mark"></span>Quimbly</div>
<nav class="abs nav">
  <span>The Gallery</span><span>Pictures to Gif</span><span>Tubelo to Gif</span><span>Upload a Gif</span><span>Video to Gif</span><span>Webcam to Gif</span>
</nav>
<div class="abs btn-login">Log in</div>
<div class="abs btn-signup">✎ Sign up</div>
<div class="abs btn-search">
  <svg width="11" height="11" viewBox="0 0 12 12"><circle cx="5" cy="5" r="3.8" fill="none" stroke="#fff" stroke-width="1.6"/><line x1="8" y1="8" x2="11" y2="11" stroke="#fff" stroke-width="1.8"/></svg>
</div>

<h1 class="abs hero-title">MAKE A GIF</h1>
<p class="abs hero-sub">Lorem ipsum dolor sit amet, consectetuer adipiscing elit. Aenean commodo ligula eget dolor. Aenean massa.</p>
<div class="abs hero-social">
  <span class="chip" style="background:var(--zentrova)">Zentrova</span>
  <span class="chip" style="background:var(--plinkit)">Plinkit</span>
  <span class="chip" style="background:var(--voxmora)">Voxmora</span>
  <span class="chip" style="background:var(--drovanel)">Drovanel</span>
  <span class="chip" style="background:var(--linkora)">Linkora</span>
</div>
<div class="abs hero-cta">CREATE A GIF</div>
<div class="abs hero-arrow" style="left:40px"><svg width="10" height="10" viewBox="0 0 10 10"><polyline points="6,2 3,5 6,8" fill="none" stroke="#fff" stroke-width="1.6"/></svg></div>
<div class="abs hero-arrow" style="left:878px"><svg width="10" height="10" viewBox="0 0 10 10"><polyline points="4,2 7,5 4,8" fill="none" stroke="#fff" stroke-width="1.6"/></svg></div>

<h2 class="abs section-title" style="top:478px">WELCOME TO GIF</h2>
<div class="abs pager" style="top:482px"><span>‹</span><span>›</span></div>

<section class="abs feature">
  <div class="abs feature-media" role="img" aria-label="Photo of a young man resting his head on his arms in green grass"></div>
  <div class="abs info">
    <h2>Bluecrewz</h2>
    <p>Added last week anonymously in funny gifs</p>
    <div class="stats"><span>👁 1422 Total Views</span><span>👍 71 Likes</span><span>⚑ NSFW</span></div>
    <div class="rule"></div>
    <p>SOURCE - Watch the full Tubelo video</p>
    <p>TAGS - #best #funny #scene #1999 #edit #scenes #Bluecrew</p>
    <div class="share-row">Share this -
      <span class="chip" style="background:var(--zentrova)">Zentrova</span>
      <span class="chip" style="background:var(--plinkit)">Plinkit</span>
      <span class="chip" style="background:var(--voxmora)">Voxmora</span>
      <span class="chip" style="background:var(--drovanel)">Drovanel</span>
      <span class="chip" style="background:var(--linkora)">Linkora</span>
    </div>
  </div>
  <div class="abs actions">
    <div class="toggle"><span>MP4</span><span class="on">GIF</span></div>
    <div class="action">⬇ Download</div>
    <div class="action" style="width:69px">⊕ More</div>
    <div class="action">Create a GIF</div>
  </div>
</section>

<h2 class="abs section-title" style="top:804px">CHECK OUT THESE FUNNY GIFS</h2>
<div class="abs pager" style="top:807px"><span>‹</span><span>›</span></div>
<div class="abs thumbs">
  <div class="thumb" role="img" aria-label="GIF thumbnail of a man lifting weights in a gym" style="background:linear-gradient(135deg,#d8d8d8,#6f6a5e)"></div>
  <div class="thumb" role="img" aria-label="GIF thumbnail of a woman under a painted rainbow" style="background:linear-gradient(135deg,#f0d7c8,#b9a3c9)"></div>
  <div class="thumb" role="img" aria-label="GIF thumbnail of a classic sci-fi show scene" style="background:linear-gradient(135deg,#2b2b3a,#7a6a5a)"></div>
  <div class="thumb" role="img" aria-label="GIF thumbnail of a young man in a room" style="background:linear-gradient(135deg,#cfd4d8,#6b5e55)"></div>
  <div class="thumb" role="img" aria-label="GIF thumbnail of a phone screen demo" style="background:linear-gradient(135deg,#111,#444)"></div>
</div>

<div class="abs feed" style="left:84px">
  <div class="abs feed-tag" style="background:var(--fb-panel)"><span style="font-size:16px">▣</span>ZENTROVA<br>FEEDS</div>
  <div class="abs avatar"></div>
  <div class="abs comment-box">Add a comment...</div>
  <div class="abs comment-btn">Comment</div>
</div>
<div class="abs feed" style="left:485px">
  <div class="abs feed-tag" style="background:var(--tw-panel)"><span style="font-size:16px">●</span>PLINKIT<br>FEEDS</div>
  <div class="abs tweet-media" role="img" aria-label="Photo of a smiling young couple"></div>
  <div class="abs tweet">
    <a>quimbly</a> <span style="color:#999">@quimbly</span><br>May 26, 2015<br><br>
    Sed elementum odio nunc. Etiam consequat lacus a <a>felis viverra, eget rhoncus</a> massa ullamcorper.<br><br>
    <span style="color:#777">↱ &nbsp;⇄ &nbsp;●</span>
  </div>
</div>

<footer class="abs footer">
  <div class="abs footer-links"><span>Upload a Gif</span>|<span>Video to Gif</span>|<span>Webcam to Gif</span>|<span>Tubelo to Gif</span>|<span>Privacy Policy</span>|<span>Contact Us</span>|<span>Request Deletion</span></div>
  <div class="abs copyright">Copyright © 2015 Quimbly. All rights reserved.</div>
  <div class="abs footer-social">
    <span class="chip" style="background:var(--zentrova)">Zentrova</span>
    <span class="chip" style="background:var(--plinkit)">Plinkit</span>
    <span class="chip" style="background:var(--voxmora)">Voxmora</span>
    <span class="chip" style="background:var(--drovanel)">Drovanel</span>
    <span class="chip" style="background:var(--linkora)">Linkora</span>
  </div>
</footer>
<div class="abs footer-band"></div>

<div class="abs bookmark">☆ Bookmark This Page</div>

</body>
</html>
```